Business Card Design for sports performance / psychology company

You can see my website that this is based upon here:
http://www.trelvanedge.co.uk

More than happy to answer any additional questions that you might have

** Happy for any images from Pixelvault to be used. If I go with your design I will purchase the image for you to use

Target Market(s)

Football players

Industry/Entity Type

Business

Contact Information for Business Card

Name: Clive Arnott
Title: Clinical Hypnotherapist & Strategist
Email address: clive@trelvanedge.co.uk
Tel: 07912486015

Font styles to use
Other font styles liked:
• Same font as on website. I'm not actually sure what it is

Requirements
Must have
• Tagline:
• Ability x Form = Performance
• Don't put form down to chance
Nice to have
• Happy for designers to be creative
Should not have

```html
<!DOCTYPE html>
<html lang="en">
<head>
<meta charset="utf-8">
<title>Trelvan Edge – Business Card</title>
<link href="https://fonts.googleapis.com/css2?family=Jost:wght@400&family=Lato:wght@400&display=swap" rel="stylesheet">
<style>
  :root {
    --backdrop: #1f1f1f;
    --navy: #241f4a;
    --white: #ffffff;
    --ink-soft: #2c2a4a;
    --stadium-top: #2e3a4c;
    --stadium-mid: #6b7787;
    --pitch: #3f8a34;
    --pitch-dark: #2f6e27;
  }
  * { box-sizing: border-box; margin: 0; padding: 0; }
  html, body { width: 1189px; height: 1200px; overflow: hidden; background: var(--backdrop); }
  .canvas { position: relative; width: 1189px; height: 1200px; }
  .card {
    position: absolute; left: 171px; width: 856px; height: 487px; overflow: hidden;
    box-shadow: 6px 8px 14px rgba(0,0,0,0.55);
  }
  .card--front { top: 68px; }
  .card--back { top: 627px; background: var(--white); }

  .front-photo {
    position: absolute; inset: 0;
    background:
      linear-gradient(to bottom, transparent 72%, var(--pitch) 72.5%, var(--pitch-dark) 100%),
      radial-gradient(ellipse at 50% 20%, var(--stadium-mid) 0%, var(--stadium-top) 75%);
  }
  .front-brand {
    position: absolute; left: 0; right: 0; top: 0; text-align: center; color: var(--white);
  }
  .front-mark {
    display: block; width: 56px; height: 56px; margin: 92px auto 0;
    border-radius: 50%; background: var(--white);
  }
  .front-name {
    margin-top: 28px; font-family: "Jost", sans-serif; font-weight: 400;
    font-size: 57px; letter-spacing: 1px; line-height: 1;
  }
  .front-tagline {
    margin-top: 40px; font-family: "Lato", sans-serif; font-size: 28px; letter-spacing: 0.3px;
  }

  .back-band { position: absolute; left: 0; top: 0; width: 106px; height: 100%; background: var(--navy); }
  .back-rule { position: absolute; left: 108px; top: 0; width: 7px; height: 100%; background: var(--navy); }
  .back-mark {
    position: absolute; left: 43px; top: 64px; width: 112px; height: 112px; border-radius: 50%;
    background: var(--navy); border: 8px solid var(--white);
  }
  .back-name {
    position: absolute; left: 188px; top: 88px; font-family: "Jost", sans-serif; font-weight: 400;
    font-size: 50px; color: var(--navy); letter-spacing: 1px; line-height: 1;
  }
  .person { position: absolute; left: 200px; top: 278px; font-family: "Lato", sans-serif; color: var(--ink-soft); }
  .person-name { font-size: 33px; color: var(--navy); line-height: 1.1; }
  .person-title { font-size: 22px; margin-top: 2px; }
  .contacts { position: absolute; left: 200px; top: 366px; list-style: none; font-family: "Lato", sans-serif; color: var(--ink-soft); }
  .contacts li { display: flex; align-items: center; height: 28px; font-size: 23px; }
  .contacts svg { width: 23px; height: 23px; margin-right: 12px; flex: none; }
</style>
</head>
<body>
<main class="canvas">
  <section class="card card--front">
    <div class="front-photo" role="img" aria-label="Floodlit football stadium with the centre circle of the pitch in the foreground"></div>
    <div class="front-brand">
      <span class="front-mark"></span>
      <h1 class="front-name">TRELVAN EDGE</h1>
      <p class="front-tagline">Because Focus Builds Champions</p>
    </div>
  </section>

  <section class="card card--back">
    <div class="back-band"></div>
    <div class="back-rule"></div>
    <span class="back-mark"></span>
    <h2 class="back-name">TRELVAN EDGE</h2>
    <div class="person">
      <p class="person-name">Clive Arnott</p>
      <p class="person-title">Clinical Hypnotherapist &amp; Strategist</p>
    </div>
    <ul class="contacts">
      <li>
        <svg viewBox="0 0 24 24" aria-hidden="true"><rect width="24" height="24" fill="#241f4a"/><path d="M5 9c0-2 3-3 7-3s7 1 7 3v1h-4V9H9v1H5z M7 11h10l1 7H6z" fill="#fff"/></svg>
        07912486015
      </li>
      <li>
        <svg viewBox="0 0 24 24" aria-hidden="true"><rect width="24" height="24" fill="#241f4a"/><rect x="4" y="7" width="16" height="11" fill="none" stroke="#fff" stroke-width="1.6"/><path d="M4 7l8 6 8-6" fill="none" stroke="#fff" stroke-width="1.6"/></svg>
        clive@trelvanedge.co.uk
      </li>
      <li>
        <svg viewBox="0 0 24 24" aria-hidden="true"><rect width="24" height="24" fill="#241f4a"/><circle cx="12" cy="12" r="7" fill="none" stroke="#fff" stroke-width="1.5"/><ellipse cx="12" cy="12" rx="3" ry="7" fill="none" stroke="#fff" stroke-width="1.3"/><path d="M5 12h14M6 8.5h12M6 15.5h12" stroke="#fff" stroke-width="1.2"/></svg>
        www.trelvanedge.co.uk
      </li>
    </ul>
  </section>
</main>
</body>
</html>
```